Annual review for The Harrow Collective

The Harrow Collective is a small public relations agency in London specialising in corporate and public affairs. Most of our work is international and we have a strong connection to South Africa. We would like to prepare a short annual review for 2016. The review will serve as both a review of our activities in 2016, and as a credentials document. Content then will include:
1. An introduction to the business
2. Who we are
3. Projects and clients undertaken in 2016
4. News and views
We imagine it will be used mostly as a pdf but would like it to be suitable for print. We envisage it to be about 8 pages long. The design look and feel should convey a business, while small, of stature. We shall include some of our client logos but we would welcome the use of some photography / imagery to have visual impact (although we don't have very much of our own!). The corporate look and feel is white, grey and black.

Industry/Entity Type

Public Relation

Font styles to use
Sans Serif

Requirements
Must have
• My project must convey a business with flair and gravitas, that punches above its weight.
Nice to have
• Thoughtful use of imagery.

```html
<!DOCTYPE html>
<html lang="en">
<head>
<meta charset="utf-8">
<title>The Harrow Collective – Annual Review 2016</title>
<link href="https://fonts.googleapis.com/css2?family=Montserrat:wght@600&family=Open+Sans:ital,wght@0,300;0,400;0,600;1,400&display=swap" rel="stylesheet">
<style>
  :root{
    --backdrop:#c6c6c6;
    --paper:#ffffff;
    --ink:#3a3a3a;
    --ink-soft:#5a5a5a;
    --ink-muted:#8a8a8a;
    --accent:#1fa3c9;
    --rule:#9a9a9a;
    --logo-fill:#e6e6e7;
    --logo-text:#a9a9ab;
    --wave-dark:#4a4a4a;
    --wave-light:#e8e8e8;
  }
  *{box-sizing:border-box;margin:0;padding:0}
  html,body{width:1200px;height:960px;overflow:hidden}
  body{background:var(--backdrop);font-family:"Open Sans",Arial,sans-serif;color:var(--ink);position:relative}
  .spread{position:absolute;left:84px;top:102px;width:1042px;height:737px;display:flex;background:var(--paper)}
  .page{position:relative;width:521px;height:737px;background:var(--paper)}
  .page--left{border-right:1px solid #ededed}

  .brand{position:absolute;left:37px;top:47px;display:flex;align-items:center;gap:6px;
    font-family:"Montserrat",Arial,sans-serif;font-weight:600;font-size:13.5px;color:#4a4a4a}
  .brand__mark{width:17px;height:17px;border:1.2px solid #4a4a4a;border-radius:50%}

  .page-title{position:absolute;left:62px;top:112px;font-weight:300;font-size:32px;line-height:44px;color:#444;letter-spacing:-.2px}
  .page-intro{position:absolute;left:62px;top:164px;width:400px;font-weight:300;font-size:14px;line-height:17.5px;color:#555}
  .header-rule{position:absolute;left:0;top:236px;width:521px;border-top:1px solid var(--rule)}

  .body-intro{position:absolute;left:62px;top:264px;width:382px;font-size:7.4px;line-height:12.3px;color:var(--ink-soft)}

  .case{position:absolute;width:172px;font-size:7.4px;line-height:12.3px;color:var(--ink-soft)}
  .case__label{font-weight:600;color:var(--ink);text-transform:uppercase}
  .case__title{color:var(--accent);font-weight:600}
  .case__org{font-weight:600;color:var(--ink)}
  .case__date{font-style:italic;margin-bottom:12.3px}
  .case--1{left:62px;top:335px}
  .case--2{left:62px;top:494px}
  .case--3{left:272px;top:335px}
  .case--4{left:272px;top:494px;width:184px}

  .footer{position:absolute;top:701px;font-size:5.4px;letter-spacing:1.4px;color:var(--ink-muted);text-transform:uppercase}
  .footer__num{color:var(--accent)}
  .footer--left{left:46px}
  .footer--url{text-transform:lowercase;letter-spacing:1.2px}
  .page--left .footer--url{left:366px}
  .page--right .footer--left{left:51px}
  .page--right .footer--url{left:370px}

  .hero{position:absolute;left:0;top:0;width:521px;height:236px;
    background:radial-gradient(ellipse at 45% 75%,#6a6a6a 0%,transparent 40%),
               linear-gradient(115deg,var(--wave-dark) 0%,#7c7c7c 35%,#cfcfcf 55%,var(--wave-light) 75%,#f6f6f6 100%)}

  .clients-label{position:absolute;left:64px;top:447px;font-weight:300;font-size:16px;color:#555}
  .logo{position:absolute;width:37px;height:37px;margin:-18.5px 0 0 -18.5px;border-radius:50%;
    background:var(--logo-fill);color:var(--logo-text);font-size:7.5px;font-weight:600;
    display:flex;align-items:center;justify-content:center}
</style>
</head>
<body>
<div class="spread">
  <section class="page page--left">
    <div class="brand"><span class="brand__mark"></span>The Harrow Collective</div>
    <h1 class="page-title">Who we work with</h1>
    <p class="page-intro">The Harrow Collective works with a range of clients, including consultancies, law firms, charities and individuals.</p>
    <div class="header-rule"></div>

    <p class="body-intro">In providing sustainability, corporate and public affairs advice, the nature of our work is often confidential. That said, we have experience in researching and producing policy reports and papers which are often published.&nbsp; Below is a small example of past work undertaken by members of the team which is in the public domain:</p>

    <article class="case case--1">
      <div class="case__label">Case Study 1</div>
      <div class="case__title">Publication: Rivers, Resources and Resilience</div>
      <div class="case__org">Council for Meridian Economic<br>Policy (CMEP)</div>
      <div class="case__date">September 2014</div>
      <p>The Harrow Collective wrote the policy toolbox chapters and gathered international case studies for the CMEP report on Rivers, Resources and Resilience due to be published in the coming months.</p>
    </article>

    <article class="case case--2">
      <div class="case__label">Case Study 2</div>
      <div class="case__title">Publication: Rivers, Resources and Resilience</div>
      <div class="case__org">Government of the Republic of Veloria and the Tidewell Water Alliance</div>
      <div class="case__date">March 2012</div>
      <p>This report was the first major output of a project on rivers and resilience, led by the Government of the Republic of Veloria and the Tidewell Water Alliance.</p>
    </article>

    <article class="case case--3">
      <div class="case__label">Case Study 3</div>
      <div class="case__title">Publication: Clear Currents: Water and Prosperity in Africa</div>
      <div class="case__org">Tidewell Water Alliance and the Northmere Ministry for External Affairs</div>
      <div class="case__date">November 2011</div>
      <p>Clear Currents focused on the importance of water resources to development and prosperity in the continent.</p>
    </article>

    <article class="case case--4">
      <div class="case__label">Case Study 4</div>
      <div class="case__title">Publication: Leading by Example - Stewardship in Public Operations Review 2009</div>
      <div class="case__org">Ashcombe Stewardship Commission</div>
      <div class="case__date">July 2010</div>
      <p>Leading by Example: achieving sustainability in operations and procurement, was the fifth of the Ashcombe Stewardship Commission’s annual watchdog reports which scrutinised Government’s progress towards more sustainable operations.</p>
    </article>

    <div class="footer footer--left"><span class="footer__num">03</span> &nbsp;|&nbsp; Annual Review 2016</div>
    <div class="footer footer--url">www.harrowcollective.example</div>
  </section>

  <section class="page page--right">
    <div class="hero" role="img" aria-label="Black and white photograph of a large breaking ocean wave curling over with white spray"></div>

    <h2 class="clients-label">Clients</h2>
    <div class="logo" style="left:188px;top:363px">LOGO</div>
    <div class="logo" style="left:305px;top:363px">LOGO</div>
    <div class="logo" style="left:425px;top:363px">LOGO</div>
    <div class="logo" style="left:188px;top:456px">LOGO</div>
    <div class="logo" style="left:305px;top:456px">LOGO</div>
    <div class="logo" style="left:425px;top:456px">LOGO</div>
    <div class="logo" style="left:188px;top:556px">LOGO</div>
    <div class="logo" style="left:305px;top:556px">LOGO</div>
    <div class="logo" style="left:425px;top:556px">LOGO</div>

    <div class="footer footer--left"><span class="footer__num">04</span> &nbsp;|&nbsp; Annual Review 2016</div>
    <div class="footer footer--url">www.harrowcollective.example</div>
  </section>
</div>
</body>
</html>
```